Design a Google site for a travel agency

I own a travel agency and I would like to have a Google site built for my company called Harborquestjourneys.com by Bright Path Holidays. Our specialty Cruising and adventure. We create a lot of custom tour of Europe and Peru. Our Adventure tours targets mainly women from 25 to 65. I would like to site especially the cruise to appeal to family but also upscale more expensive upscale clientele.
Updates

I would like to shift away from create a new site with multiple pages to one simple Google Site page with a Contact us page and testimonials. The sites theme is Cruise & Adventure Travel. We specialize in selling cruises and building custom travel tours around the world.

Target Market(s)

Cruisers and adventure travelers for women from 25 to 70

Industry/Entity Type

travel industry with a focus on cruising and adventure travel

Coding

Coded - Design and coding required

Number of Pages Required

5+ page

Font styles to use
Serif
Sans Serif

Requirements
Must have
• Home page, Cruise, Adventure Tours, Testimonials, About Us
Nice to have
• Auto place https://www.brightpathholidays.ca/offers into the site.
Should not have
• beach resorts

```html
<!DOCTYPE html>
<html lang="en">
<head>
<meta charset="utf-8">
<title>Bright Path Holidays</title>
<link href="https://fonts.googleapis.com/css2?family=Cinzel:wght@400;500&family=Open+Sans:wght@400;600&display=swap" rel="stylesheet">
<style>
:root{
  --orange:#f39519;
  --orange-title:#e38a28;
  --green:#78b344;
  --blue:#2f8fcb;
  --tint:#eff3ec;
  --text:#222;
  --star:#f5c400;
  --tile:#f2f3f5;
  --footer:#141414;
}
*{margin:0;padding:0;box-sizing:border-box}
html,body{width:1200px;height:4728px;overflow:hidden}
body{font-family:"Open Sans",Arial,sans-serif;color:var(--text);background:#fff;font-size:16px}
.section-title{font-family:"Cinzel",Georgia,serif;font-weight:500;font-size:36px;text-align:center;letter-spacing:1px}
.section-sub{text-align:center;font-size:16px;margin-top:22px;line-height:30px}
.btn{display:block;margin:0 auto;width:190px;height:52px;line-height:52px;background:var(--orange);color:#fff;font-weight:600;font-size:16px;text-align:center;border-radius:6px;text-decoration:none}
.photo{display:block}

/* hero */
.hero{position:relative;height:616px;background:linear-gradient(180deg,#2f3e55 0%,#5b5650 35%,#6b5138 65%,#3e3225 100%)}
.nav{position:absolute;top:0;left:0;right:0;height:110px;display:flex;align-items:center;justify-content:space-between;padding:0 70px 0 72px}
.brand{display:flex;align-items:center;gap:10px;color:#f1c35a;font-family:"Open Sans",Arial,sans-serif;font-size:16px;font-weight:600}
.brand-dot{width:14px;height:14px;border-radius:50%;background:#f1c35a}
.menu{display:flex;gap:18px;color:#fff;font-size:13.5px}
.hero-title{position:absolute;top:215px;left:0;right:0;text-align:center;color:#fff;font-family:"Cinzel",Georgia,serif;font-size:68px;line-height:92px;font-weight:400;text-shadow:0 2px 8px rgba(0,0,0,.35)}

/* experiences */
.experiences{height:964px;padding-top:88px}
.experiences .section-title{color:var(--orange-title)}
.exp-grid{display:grid;grid-template-columns:310px 310px 310px;column-gap:21px;row-gap:25px;width:972px;margin:50px auto 0}
.exp-card .photo{height:240px}
.stars{text-align:center;color:var(--star);font-size:15px;letter-spacing:2px;margin-top:14px}
.exp-name{text-align:center;font-size:16px;margin-top:3px}

/* promotions */
.promotions{height:655px;background:var(--tint);padding-top:56px}
.promotions .section-title{color:var(--green)}
.promotions .btn{margin-top:26px}
.promo-grid{display:flex;justify-content:space-between;width:975px;margin:48px auto 0}
.promo-card{width:459px}
.promo-card .photo{height:248px}
.promo-card p{text-align:center;margin-top:25px;font-size:16px}

/* blogs */
.blogs{height:708px;padding-top:78px}
.blogs .section-title{color:var(--blue)}
.blogs .btn{margin-top:20px}
.blog-grid{display:flex;justify-content:space-between;width:974px;margin:64px auto 0}
.blog-card{width:310px}
.blog-card .photo{height:240px}
.blog-card p{text-align:center;margin-top:28px;font-size:16px;line-height:30px}

/* newsletter */
.newsletter{height:375px;background:var(--tint);padding-top:82px}
.newsletter .section-title{color:var(--green)}
.newsletter .section-sub{width:930px;margin:30px auto 0}
.newsletter .btn{margin-top:30px}

/* magazines */
.magazines{height:1197px;padding-top:86px}
.magazines .section-title{color:var(--blue)}
.mag-grid{display:flex;justify-content:space-between;width:975px;margin:54px auto 0}
.mag-stack{display:flex;flex-direction:column;gap:17px}
.mag-stack .photo{width:392px;height:248px}
.mag-feature{width:565px;height:513px}
.partners-title{color:var(--green);margin-top:118px}
.partner-grid{display:flex;justify-content:space-between;width:976px;margin:55px auto 0}
.partner{width:228px;height:162px;background:var(--tile);display:flex;align-items:center;justify-content:center}

/* footer */
.footer{height:213px;background:var(--footer);color:#fff;padding-top:52px;position:relative}
.contact-row{display:flex;width:1100px;margin:0 auto}
.contact-item{flex:1;text-align:center;font-size:16px;line-height:30px}
.copyright{position:absolute;bottom:10px;left:0;right:0;text-align:center;font-size:16px}
</style>
</head>
<body>

<header class="hero" role="img" aria-label="Photo of an ornate sandstone palace with domed towers under a cloudy evening sky">
  <nav class="nav">
    <div class="brand"><span class="brand-dot"></span>Bright Path Holidays</div>
    <div class="menu"><span>About Us</span><span>Experiences</span><span>Tours</span><span>Offers</span><span>Blogs</span><span>Contest</span><span>Testimonials</span><span>Exclusives</span><span>Contact</span><span>Book Now</span></div>
  </nav>
  <h1 class="hero-title">Welcome To<br>Bright Path Holidays</h1>
</header>

<section class="experiences">
  <h2 class="section-title">Popular Travel Experiences</h2>
  <p class="section-sub">Some of our most popular travel categories</p>
  <div class="exp-grid">
    <div class="exp-card"><div class="photo" role="img" aria-label="Couple holding a rainbow flag on a sunny beach" style="background:linear-gradient(180deg,#9fc6e4 0%,#d9e6ea 50%,#e9ddc6 100%)"></div><div class="stars">★★★★★</div><div class="exp-name">LGBTQ</div></div>
    <div class="exp-card"><div class="photo" role="img" aria-label="Hiker with backpack looking over a green mountain valley" style="background:linear-gradient(180deg,#c9d6df 0%,#7f9a5e 45%,#4f6b33 100%)"></div><div class="stars">★★★★★</div><div class="exp-name">ADVENTURE</div></div>
    <div class="exp-card"><div class="photo" role="img" aria-label="Large white cruise ship sailing on deep blue ocean" style="background:linear-gradient(180deg,#7fa7cf 0%,#3a6d9c 45%,#1d4670 100%)"></div><div class="stars">★★★★★</div><div class="exp-name">OCEAN CRUISES</div></div>
    <div class="exp-card"><div class="photo" role="img" aria-label="Breakfast tray with newspaper on a private balcony over the sea" style="background:linear-gradient(180deg,#a9bccb 0%,#d3d8da 55%,#eaeaea 100%)"></div><div class="stars">★★★★★</div><div class="exp-name">LUXURY</div></div>
    <div class="exp-card"><div class="photo" role="img" aria-label="Group practising yoga on a misty beach" style="background:linear-gradient(180deg,#b9bfc3 0%,#9ea4a6 55%,#85817a 100%)"></div><div class="stars">★★★★★</div><div class="exp-name">WELLNESS</div></div>
    <div class="exp-card"><div class="photo" role="img" aria-label="River cruise boat docked by a hillside village" style="background:linear-gradient(180deg,#8cb0d6 0%,#4d7a3c 45%,#8d8e86 75%,#4f6d7a 100%)"></div><div class="stars">★★★★★</div><div class="exp-name">RIVER CRUISES</div></div>
  </div>
</section>

<section class="promotions">
  <h2 class="section-title">Featured Promotions</h2>
  <p class="section-sub">The best deals happening now. Act fast, they won't last long!</p>
  <a class="btn" href="https://www.brightpathholidays.ca/offers">View All Offers</a>
  <div class="promo-grid">
    <div class="promo-card"><div class="photo" role="img" aria-label="Country music concert on a lit stage" style="background:linear-gradient(180deg,#1c2740 0%,#5a3a55 45%,#a0563c 70%,#1a1a24 100%)"></div><p>Starting from $879CAD Per Person - Nashville</p></div>
    <div class="promo-card"><div class="photo" role="img" aria-label="Riders on a roller coaster against a blue sky" style="background:linear-gradient(180deg,#2a49a8 0%,#4d6cc4 50%,#7a6b5e 100%)"></div><p>Lakeshore Thrill Park - A Family Escape</p></div>
  </div>
</section>

<section class="blogs">
  <h2 class="section-title">Travel Blogs, Tips &amp; Stories</h2>
  <p class="section-sub">Find inspiration for your next vacation of a lifetime</p>
  <a class="btn" href="#">View All Travel Blogs</a>
  <div class="blog-grid">
    <div class="blog-card"><div class="photo" role="img" aria-label="Sunset over a calm sea seen from a ship deck railing" style="background:linear-gradient(180deg,#e0875a 0%,#9a95a3 35%,#5d6f82 60%,#3e4f60 100%)"></div><p>Going Solo: The Best New Cruise Ship for Single Travellers</p></div>
    <div class="blog-card"><div class="photo" role="img" aria-label="Ruined stone castle on a grassy hill at golden hour" style="background:linear-gradient(180deg,#4a3a2a 0%,#7a5a36 45%,#5b4a2a 75%,#3b3a1c 100%)"></div><p>Why Ireland Should Be On Your Bucket List</p></div>
    <div class="blog-card"><div class="photo" role="img" aria-label="Aerial view of a cruise ship deck with colourful water park" style="background:linear-gradient(180deg,#5fa8d6 0%,#3d8ab8 40%,#c7a060 70%,#3a6c8a 100%)"></div><p>4 Reasons a Cruise Makes the Best Family Vacation</p></div>
  </div>
</section>

<section class="newsletter">
  <h2 class="section-title">Get Amazing Offers &amp; Save Big</h2>
  <p class="section-sub">Get the best travel deals &amp; specials delivered directly to your inbox. Sign up to receive incredible offers on cruises, adventures, all-inclusives, coach tours, family vacations and holidays of a lifetime.</p>
  <a class="btn" href="#">Subscribe Now</a>
</section>

<section class="magazines">
  <h2 class="section-title">Award Winning Magazines</h2>
  <p class="section-sub">Click the magazine cover of your choice to read more.</p>
  <div class="mag-grid">
    <div class="mag-stack">
      <div class="photo" role="img" aria-label="Luxury travel magazine cover with palm trees and an infinity pool at sunset" style="background:linear-gradient(180deg,#5e7b88 0%,#c48c5a 55%,#8a5a34 100%)"></div>
      <div class="photo" role="img" aria-label="Cruise magazine cover with a couple on deck at sunset" style="background:linear-gradient(180deg,#6f8fa6 0%,#c7a07a 50%,#7a5a40 100%)"></div>
    </div>
    <div class="photo mag-feature" role="img" aria-label="Asia travel magazine cover with a portrait in traditional dress and sunflowers" style="background:linear-gradient(180deg,#2c2a2a 0%,#6a4a30 40%,#b2743c 70%,#7c2a2a 100%)"></div>
  </div>
  <h2 class="section-title partners-title">Award Winning Magazines</h2>
  <div class="partner-grid">
    <div class="partner"><svg width="70" height="44"><rect width="70" height="44" rx="4" fill="#c9cdd3"/></svg></div>
    <div class="partner"><svg width="60" height="44"><rect width="60" height="44" rx="4" fill="#c9cdd3"/></svg></div>
    <div class="partner"><svg width="84" height="44"><rect width="84" height="44" rx="4" fill="#c9cdd3"/></svg></div>
    <div class="partner"><svg width="56" height="44"><rect width="56" height="44" rx="4" fill="#c9cdd3"/></svg></div>
  </div>
</section>

<footer class="footer">
  <div class="contact-row">
    <div class="contact-item">Email Us:<br>hello@brightpathholidays.ca</div>
    <div class="contact-item">Call Us:<br>506-555-0142</div>
    <div class="contact-item">Address:<br>14 Marlow Ave, Riverton, NB, E3A 2K4,<br>Canada</div>
  </div>
  <p class="copyright">2022 Bright Path Holidays. All Rights Reserved.</p>
</footer>

</body>
</html>
```